Business Cards for new orthopaedic surgery practice

My husband and I are starting our own orthopaedic surgery practice. We are looking for a business card that is uniform, but one will have my name/title and the other will have his. You can just create one design with my name on it for now. But when I choose your design as the winning design I will ask that you add another copy with his name/title.

We are looking for classy, simple, elite all in one. We like dark blues/a little gold/yellow. Something that goes with our logo. We want our logo incorporated. Here is all the info you need:
Business name: RV Bone & Vitality Center
Location: 38517 North Willowmere Ave
Harbor Pines, FL 33490
Phone: 954-218-4063
Fax: 954-582-7341
Email: info@myrvbonecare.example

Names: Lydia Vance, M.D.
Board Certified Hand and Upper Extremity Surgeon

Ebo Dansu, M.D.
Board Certified Hip & Knee Replacement/General Orthopaedic Surgeon

Can decide what you want to put on the back. Maybe a slogan:
Grounded in Care. Centered on You

I am just going to upload our logo. The only thing is if we select you as the winning design, the location, and phone numbers may change. We will need your help to update that once fully solidified.

Industry/Entity Type

Medical

Contact Information for Business Card

Colors
0054AA
0677BA
7BADD7
CADEEF
E8F1F8
0094D4
00A9DD
6FCCEA
C7EBF8
E9F6FB

Requirements
Must have
• class, appeal,
Should not have
• We want to air on the side of masculine if we are looking at masculine vs. feminine feel. But we still want it classy, sophisticated, and something we will love

```html
<!DOCTYPE html>
<html lang="en">
<head>
<meta charset="utf-8">
<title>RV Bone &amp; Vitality Center – Business Card</title>
<link rel="stylesheet" href="https://fonts.googleapis.com/css2?family=Montserrat:wght@400;500;700&display=swap">
<style>
  :root {
    --navy: #17234a;
    --navy-deep: #1c2a50;
    --navy-soft: #2a3a66;
    --gold: #c9a25a;
    --ink: #1a1a1a;
    --paper: #ffffff;
    --backdrop: #e6e6e8;
  }
  * { margin: 0; padding: 0; box-sizing: border-box; }
  html, body {
    width: 1200px; height: 1108px; overflow: hidden;
    background: var(--backdrop);
    font-family: "Montserrat", Arial, sans-serif;
  }
  .canvas { position: relative; width: 1200px; height: 1108px; }

  .card { position: absolute; }
  .card--front { left: 219px; top: 50px; width: 775px; height: 474px; background: var(--paper); }
  .card--back { left: 217px; top: 568px; width: 777px; height: 457px; background: var(--navy-deep); }

  .brand-mark {
    position: absolute; left: 137px; top: 140px; width: 200px; height: 200px;
    border: 2px solid var(--gold); border-radius: 50%;
    display: flex; align-items: center; justify-content: center; text-align: center;
  }
  .brand-mark__name {
    color: var(--navy); font-weight: 700; font-size: 19px; line-height: 1.3;
    text-transform: uppercase; letter-spacing: 1px; padding: 0 22px;
  }

  .divider { position: absolute; left: 368px; top: 127px; width: 2px; height: 233px; background: var(--navy); }

  .details { position: absolute; left: 390px; top: 124px; color: var(--ink); }
  .details__name { font-size: 29px; font-weight: 700; color: var(--navy); line-height: 1.2; }
  .details__name .credential { color: var(--gold); }
  .details__title { font-size: 17px; line-height: 22px; margin-top: 2px; }
  .details__address { font-size: 17px; line-height: 22px; margin-top: 22px; }
  .contact-list { list-style: none; margin-top: 16px; }
  .contact-list li { display: flex; align-items: center; font-size: 17px; height: 27px; }
  .contact-list svg { width: 14px; height: 14px; margin-right: 9px; fill: var(--gold); }

  .tagline-rule {
    position: absolute; left: 0; right: 0; top: 411px;
    display: flex; align-items: center;
  }
  .tagline-rule::before, .tagline-rule::after {
    content: ""; flex: 1; height: 2px; background: var(--gold);
  }
  .tagline { padding: 0 6px; color: var(--navy); font-weight: 700; font-size: 17px; white-space: nowrap; }

  .back-mark {
    position: absolute; left: 238px; top: 78px; width: 300px; height: 300px;
    border: 3px solid var(--navy-soft); border-radius: 50%;
    display: flex; align-items: center; justify-content: center; text-align: center;
  }
  .back-mark__name {
    color: var(--navy-soft); font-weight: 700; font-size: 29px; line-height: 1.3;
    text-transform: uppercase; letter-spacing: 2px; padding: 0 34px;
  }
</style>
</head>
<body>
<main class="canvas">

  <section class="card card--front" aria-label="Business card front">
    <div class="brand-mark">
      <span class="brand-mark__name">RV Bone &amp; Vitality Center</span>
    </div>

    <div class="divider"></div>

    <div class="details">
      <h1 class="details__name">Lydia Vance, <span class="credential">M.D.</span></h1>
      <p class="details__title">Board Certified Hand and<br>Upper Extremity Surgeon</p>
      <p class="details__address">38517 North Willowmere Ave<br>Harbor Pines, FL 33490</p>
      <ul class="contact-list">
        <li>
          <svg viewBox="0 0 16 16" aria-hidden="true"><path d="M2 5c0-2 2-3 6-3s6 1 6 3v1h-3V5H5v1H2zM4 7h8l2 6H2z"/></svg>
          954-218-4063
        </li>
        <li>
          <svg viewBox="0 0 16 16" aria-hidden="true"><path d="M4 1h8v4H4zM1 6h14v6h-3v3H4v-3H1zM5 10v4h6v-4z"/></svg>
          954-582-7341
        </li>
        <li>
          <svg viewBox="0 0 16 16" aria-hidden="true"><path d="M1 3h14v1L8 9 1 4zM1 6l7 5 7-5v7H1z"/></svg>
          info@myrvbonecare.example
        </li>
      </ul>
    </div>

    <div class="tagline-rule">
      <p class="tagline">Grounded in Care. Centered on You</p>
    </div>
  </section>

  <section class="card card--back" aria-label="Business card back">
    <div class="back-mark">
      <span class="back-mark__name">RV Bone &amp; Vitality Center</span>
    </div>
  </section>

</main>
</body>
</html>
```